Boutique Store Selling Antiques and Unique Finds

I need a Web Page designed for my Store Called "Willow Lane". I would like a very classic, muted design that looks European when pulled up. I will be selling Antiques from all over the world and Unique finds that have reproduced. I will also be selling high-end purses and jewelry with unique, reasonable products for the every-day buyer as well.

Target Market(s)

25-70 year old men and women;)

Coding

Coded - Design and coding required

Number of Pages Required

1 page

Colors

Designer to choose only greyscale colors for use in the design.

Requirements
Must have
• I want it

```html
<!DOCTYPE html>
<html lang="en">
<head>
<meta charset="utf-8">
<title>Willow Lane — Antiques and Unique Finds</title>
<link rel="stylesheet" href="https://fonts.googleapis.com/css2?family=Cinzel:wght@400;600;700&family=Open+Sans:wght@400;600;700&display=swap">
<style>
:root{
  --cream:#f2f0ed;
  --cream-light:#f7f6f4;
  --ink:#1a1a1a;
  --text:#333;
  --muted:#666;
  --accent:#3d3d3d;
  --accent-text:#3d3d3d;
  --star:#6e6e6e;
  --line:#d6d6d6;
  --white:#fff;
  --footer:#1b1b1b;
  --badge:#bdbdbd;
}
*{margin:0;padding:0;box-sizing:border-box}
html,body{width:1200px;height:3034px;overflow:hidden}
body{background:var(--cream);font-family:"Open Sans",sans-serif;color:var(--text);position:relative}
.abs{position:absolute}
.display{font-family:"Cinzel",serif;color:var(--ink)}
/* header */
.search{left:144px;top:28px;width:220px;height:36px;background:var(--white);border:1px solid var(--line);font-size:12px;color:#555;padding:10px 8px}
.search svg{position:absolute;right:12px;top:12px}
.brand{left:400px;top:54px;width:400px;text-align:center;font-size:28px;font-weight:600;letter-spacing:5px;white-space:nowrap}
.brand-dot{display:inline-block;width:10px;height:10px;border-radius:50%;background:var(--ink);margin-right:10px;vertical-align:middle}
.account{right:145px;top:36px;font-size:14px;color:#555;white-space:nowrap}
.account span{margin-left:16px}
.nav-band{left:0;top:110px;width:1200px;height:73px;border-top:1px solid #e2e2e2;border-bottom:1px solid #e2e2e2;background:var(--cream-light)}
.nav{top:145px;left:0;width:1200px;font-size:13px;color:var(--ink)}
.nav a{position:absolute;text-decoration:none;color:inherit;white-space:nowrap}
/* hero */
.hero{left:0;top:183px;width:1200px;height:542px;background:radial-gradient(ellipse at 50% 80%,#4a4a4a 0%,#6d6d6d 45%,#8d8d8d 100%)}
.hero-title{left:0;top:318px;width:1200px;text-align:center;font-size:64px;font-weight:600;color:var(--white);letter-spacing:8px;text-shadow:0 2px 6px rgba(0,0,0,.5);white-space:nowrap}
.hero-sub{left:0;top:405px;width:1200px;text-align:center;font-size:24px;font-weight:600;color:var(--white);text-shadow:0 2px 6px rgba(0,0,0,.6)}
.btn{background:var(--accent);color:var(--white);font-weight:700;text-align:center;text-transform:uppercase}
.hero-btn{left:515px;top:480px;width:171px;height:45px;line-height:45px;font-size:16px}
.arrow{top:415px;width:30px;height:36px;background:#2b2b2b}
.arrow svg{margin:11px 10px}
.hero-dots{left:0;top:630px;width:1200px;text-align:center}
.hero-dots i{display:inline-block;width:8px;height:8px;border-radius:50%;background:var(--white);margin:0 3px}
.hero-dots i.on{background:#2b2b2b}
.seal{left:575px;top:710px;width:50px;height:50px;border-radius:50%;background:var(--ink)}
.section-title{left:0;width:1200px;text-align:center;font-size:58px;font-weight:600}
/* products */
.band{left:0;top:902px;width:1200px;height:450px;background:var(--cream-light)}
.card{border:1px solid #cccccc;background:var(--cream-light)}
.product{top:930px;width:285px;height:413px}
.product .photo{height:318px}
.product h3{position:absolute;left:30px;top:340px;font-size:15px;font-weight:700;color:var(--ink)}
.product .price{position:absolute;left:30px;top:374px;font-size:15px;color:var(--accent-text)}
.product .stars{position:absolute;left:120px;top:377px}
.pager{left:0;width:1200px;text-align:center}
.pager i{display:inline-block;width:12px;height:12px;border-radius:50%;border:1px solid #555;margin:0 7px}
.pager i.on{background:#555}
/* email */
.email{left:145px;top:1490px;width:911px;height:333px;background:var(--white);border:1px solid #e4e4e4}
.email h2{position:absolute;left:0;top:60px;width:100%;text-align:center;font-size:60px;font-weight:600}
.email p{position:absolute;left:0;top:152px;width:100%;text-align:center;font-size:14px;color:var(--muted)}
.email .field{position:absolute;left:133px;top:211px;width:449px;height:51px;border:1px solid #ccc;font-size:12px;color:#444;padding:17px 25px}
.email .btn{position:absolute;left:593px;top:211px;width:183px;height:51px;line-height:51px;font-size:17px}
/* blog */
.post{top:2044px;width:411px;height:453px}
.post .photo{height:262px}
.post h3{position:absolute;left:35px;top:296px;font-size:15px;font-weight:700;color:var(--ink);white-space:nowrap}
.post p{position:absolute;left:35px;top:326px;width:350px;font-size:12.5px;line-height:21px;color:var(--muted)}
.post .more{position:absolute;left:35px;top:403px;font-size:14px;font-weight:700;color:var(--accent-text)}
.divider-seal{left:560px;top:2610px;width:80px;height:80px;border-radius:50%;background:var(--ink)}
/* footer */
.footer{left:0;top:2724px;width:1200px;height:310px;background:var(--footer);color:#e9e9e9}
.footer .brand-f{position:absolute;left:155px;top:100px;width:250px;text-align:center;font-family:"Cinzel",serif;font-size:22px;font-weight:600;letter-spacing:4px;color:var(--white);white-space:nowrap}
.pay{position:absolute;top:162px;left:183px;white-space:nowrap}
.pay span{display:inline-block;width:32px;height:22px;border-radius:3px;background:var(--badge);margin-right:8px}
.col{position:absolute;top:80px}
.col h4{font-size:16px;font-weight:700;color:var(--white);margin-bottom:18px;white-space:nowrap}
.col a{display:block;font-size:12px;color:#e9e9e9;text-decoration:none;margin-bottom:8px;white-space:nowrap}
.col a b{display:inline-block;width:12px;height:12px;background:#e9e9e9;margin-right:12px;vertical-align:-2px}
.legal{position:absolute;top:272px;left:0;width:1200px;text-align:center;font-size:12px}
</style>
</head>
<body>

<div class="abs search">Search
  <svg width="12" height="12" viewBox="0 0 12 12"><circle cx="5" cy="5" r="3.8" fill="none" stroke="#333" stroke-width="1.6"/><line x1="8" y1="8" x2="11" y2="11" stroke="#333" stroke-width="1.8"/></svg>
</div>
<div class="abs brand display"><span class="brand-dot"></span>Willow Lane</div>
<div class="abs account">Sign in or Register<span>
  <svg width="14" height="12" viewBox="0 0 14 12" style="vertical-align:-1px"><path d="M0 1h3l2 7h7l2-5H4" fill="none" stroke="#222" stroke-width="1.6"/><circle cx="6" cy="10.5" r="1.2" fill="#222"/><circle cx="11" cy="10.5" r="1.2" fill="#222"/></svg> Cart 0</span></div>

<div class="abs nav-band"></div>
<nav class="abs nav">
  <a style="left:201px">HOME</a><a style="left:265px">SALE</a><a style="left:321px">NEW ARRIVALS</a><a style="left:436px">ANTIQUE CROWNS</a><a style="left:575px">ABOUT</a><a style="left:648px">PRODUCTS</a><a style="left:741px">EVENTS</a><a style="left:813px">ACCESSORY</a><a style="left:910px">GIFT REGISTRY</a>
</nav>

<div class="abs hero" role="img" aria-label="Black and white photograph of an ornate antique crown with star points"></div>
<div class="abs hero-title display">Willow Lane</div>
<div class="abs hero-sub">Lorem ipsum dolor sit amet consectetur adipiscing elit</div>
<div class="abs btn hero-btn">Shop Online</div>
<div class="abs arrow" style="left:0"><svg width="10" height="14" viewBox="0 0 10 14"><path d="M8 1L2 7l6 6" fill="none" stroke="#fff" stroke-width="2"/></svg></div>
<div class="abs arrow" style="right:0"><svg width="10" height="14" viewBox="0 0 10 14"><path d="M2 1l6 6-6 6" fill="none" stroke="#fff" stroke-width="2"/></svg></div>
<div class="abs hero-dots"><i></i><i></i><i class="on"></i><i></i><i></i></div>
<div class="abs seal"></div>

<h2 class="abs section-title display" style="top:810px">New Arrivals</h2>
<div class="abs band"></div>

<div class="abs card product" style="left:146px">
  <div class="photo" role="img" aria-label="Gilded antique crown with star points resting on old books" style="background:linear-gradient(#b5b5b5,#7a7a7a 60%,#3e3e3e)"></div>
  <h3>PRODUCT NAME</h3><div class="price">$66.86</div>
  <svg class="stars" width="68" height="14" viewBox="0 0 68 14"><g fill="#6e6e6e"><polygon points="7,0 9,5 14,5 10,8 11.5,13 7,10 2.5,13 4,8 0,5 5,5"/><polygon transform="translate(13.5)" points="7,0 9,5 14,5 10,8 11.5,13 7,10 2.5,13 4,8 0,5 5,5"/><polygon transform="translate(27)" points="7,0 9,5 14,5 10,8 11.5,13 7,10 2.5,13 4,8 0,5 5,5"/><polygon transform="translate(40.5)" points="7,0 9,5 14,5 10,8 11.5,13 7,10 2.5,13 4,8 0,5 5,5"/><polygon transform="translate(54)" points="7,0 9,5 14,5 10,8 11.5,13 7,10 2.5,13 4,8 0,5 5,5"/></g></svg>
</div>
<div class="abs card product" style="left:458px">
  <div class="photo" role="img" aria-label="Jewelled antique crown on a dark stand" style="background:linear-gradient(#4e4e4e,#7d7d7d 50%,#2a2a2a)"></div>
  <h3>PRODUCT NAME</h3><div class="price">$66.86</div>
  <svg class="stars" width="68" height="14" viewBox="0 0 68 14"><g fill="#6e6e6e"><polygon points="7,0 9,5 14,5 10,8 11.5,13 7,10 2.5,13 4,8 0,5 5,5"/><polygon transform="translate(13.5)" points="7,0 9,5 14,5 10,8 11.5,13 7,10 2.5,13 4,8 0,5 5,5"/><polygon transform="translate(27)" points="7,0 9,5 14,5 10,8 11.5,13 7,10 2.5,13 4,8 0,5 5,5"/><polygon transform="translate(40.5)" points="7,0 9,5 14,5 10,8 11.5,13 7,10 2.5,13 4,8 0,5 5,5"/><polygon transform="translate(54)" points="7,0 9,5 14,5 10,8 11.5,13 7,10 2.5,13 4,8 0,5 5,5"/></g></svg>
</div>
<div class="abs card product" style="left:769px">
  <div class="photo" role="img" aria-label="Gold crown set with gemstones on a pedestal" style="background:linear-gradient(#bdbdbd,#5e5e5e 55%,#333)"></div>
  <h3>PRODUCT NAME</h3><div class="price">$66.86</div>
  <svg class="stars" width="68" height="14" viewBox="0 0 68 14"><g fill="#6e6e6e"><polygon points="7,0 9,5 14,5 10,8 11.5,13 7,10 2.5,13 4,8 0,5 5,5"/><polygon transform="translate(13.5)" points="7,0 9,5 14,5 10,8 11.5,13 7,10 2.5,13 4,8 0,5 5,5"/><polygon transform="translate(27)" points="7,0 9,5 14,5 10,8 11.5,13 7,10 2.5,13 4,8 0,5 5,5"/><polygon transform="translate(40.5)" points="7,0 9,5 14,5 10,8 11.5,13 7,10 2.5,13 4,8 0,5 5,5"/><polygon transform="translate(54)" points="7,0 9,5 14,5 10,8 11.5,13 7,10 2.5,13 4,8 0,5 5,5"/></g></svg>
</div>
<div class="abs pager" style="top:1404px"><i class="on"></i><i></i><i></i><i></i><i></i></div>

<section class="abs email">
  <h2 class="display">Join Email</h2>
  <p>Sign up to receive the latest news and updates</p>
  <div class="field">Enter Email</div>
  <div class="btn">Subscribe</div>
</section>

<h2 class="abs section-title display" style="top:1915px">Blog Posts</h2>

<article class="abs card post" style="left:170px">
  <div class="photo" role="img" aria-label="Silhouette of a crown against glowing light" style="background:radial-gradient(ellipse at 50% 45%,#9a9a9a 0%,#4a4a4a 40%,#0e0e0e 80%)"></div>
  <h3>LOREM IPSUM DOLOR SITONSECTETUR</h3>
  <p>Lorem ipsum dolor sit amet, consectetur adipiscing elit, sed do eiusmod tempor incididunt ut labore et dolore magna aliqua. Quis ipsum suspendisse ultrices gravida.</p>
  <div class="more">READ MORE</div>
</article>
<article class="abs card post" style="left:618px">
  <div class="photo" role="img" aria-label="Photograph of a pearl crown in soft haze" style="background:radial-gradient(ellipse at 55% 50%,#7a7a7a 0%,#4d4d4d 50%,#262626 100%)"></div>
  <h3>LOREM IPSUM DOLOR SITONSECTETUR</h3>
  <p>Lorem ipsum dolor sit amet, consectetur adipiscing elit, sed do eiusmod tempor incididunt ut labore et dolore magna aliqua. Quis ipsum suspendisse ultrices gravida.</p>
  <div class="more">READ MORE</div>
</article>
<div class="abs pager" style="top:2568px"><i class="on"></i><i></i><i></i><i></i><i></i></div>
<div class="abs divider-seal"></div>

<footer class="abs footer">
  <div class="brand-f">Willow Lane</div>
  <div class="pay" aria-label="Accepted payment methods"><span></span><span></span><span></span><span></span><span></span></div>
  <div class="col" style="left:492px"><h4>ABOUT</h4><a>About Us</a><a>A Family Business</a><a>Charity and Community</a><a>Press</a><a>Careers</a></div>
  <div class="col" style="left:699px"><h4>TERMS &amp; CONDITIONS</h4><a>Terms and Conditions</a><a>Privacy Policy</a><a>GDPR</a></div>
  <div class="col" style="left:967px"><h4>SOCIAL</h4><a><b></b>Snapframe</a><a><b></b>Friendwall</a><a><b></b>Pinboardly</a><a><b></b>Chirpline</a></div>
  <div class="legal">© 2021 Willow Lane.All Rights reserved &nbsp;| &nbsp;Privacy Terms &nbsp;| &nbsp;Careers &nbsp;| &nbsp;Site Map</div>
</footer>

</body>
</html>
```